Consulting company business cards

We have a base design, but would be willing to update. We have a new logo/"tag" that needs to be added. Current business card design is attached for reference into our "style."

Industry/Entity Type

Business

Contact Information for Business Card

Should contain name and title, office number, mobile number if appropriate, e-mail, website, physical address, and company logo.

Font styles to use
Other font styles liked:
• See current card design on KorvandBCard

Colors
0455a3
85acd3
aaaaaa

Requirements
Must have
• Our colors are navy blue, gray, and a lighter blue
Nice to have
• Design that I can easily drop in new names/titles as we hire employees.

```html
<!DOCTYPE html>
<html lang="en">
<head>
<meta charset="utf-8">
<title>Orvell Business Cards</title>
<link rel="stylesheet" href="https://fonts.googleapis.com/css2?family=Libre+Franklin:wght@400;600;800&display=swap">
<style>
  :root {
    --backdrop: #3b3431;
    --card: #161718;
    --card-edge: #0c0d0e;
    --navy: #0455a3;
    --navy-deep: #1d4f80;
    --light-blue: #85acd3;
    --gray: #aaaaaa;
    --silver: #8e9194;
    --white: #f2f2f2;
  }
  * { margin: 0; padding: 0; box-sizing: border-box; }
  html, body { width: 1200px; height: 864px; overflow: hidden; }
  body {
    background: var(--backdrop);
    font-family: "Libre Franklin", Arial, sans-serif;
    position: relative;
  }
  .card {
    position: absolute;
    top: 283px;
    width: 520px;
    height: 298px;
    background: var(--card);
    border-radius: 3px;
    box-shadow: 0 12px 30px rgba(0,0,0,.45);
  }
  .card--front { left: 50px; }
  .card--back { left: 630px; }

  /* front */
  .brand { position: absolute; }
  .card--front .brand { left: 92px; top: 88px; }
  .brand__name {
    font-weight: 800;
    font-size: 64px;
    letter-spacing: 2px;
    line-height: 1;
    display: flex;
    align-items: center;
    gap: 14px;
  }
  .brand__dot { width: 44px; height: 44px; border-radius: 50%; display: inline-block; }
  .brand__tag {
    font-weight: 600;
    font-size: 13.5px;
    letter-spacing: 1.4px;
    margin-top: 4px;
    margin-left: 3px;
  }
  .card--front .brand__name { color: var(--silver); }
  .card--front .brand__dot { background: #2a2c2e; }
  .card--front .brand__tag { color: #4a4d50; }
  .front__web {
    position: absolute;
    left: 95px;
    top: 206px;
    color: var(--silver);
    font-size: 14px;
    letter-spacing: 5px;
  }

  /* back */
  .card--back .brand { left: 26px; top: 104px; }
  .card--back .brand__name { color: var(--navy-deep); font-size: 44px; gap: 10px; }
  .card--back .brand__dot { width: 32px; height: 32px; background: var(--light-blue); }
  .card--back .brand__tag { color: var(--gray); font-size: 9.5px; letter-spacing: 1px; }
  .divider {
    position: absolute;
    left: 272px;
    top: 38px;
    width: 1px;
    height: 222px;
    background: linear-gradient(to bottom, transparent, #6b6e72 20%, #6b6e72 80%, transparent);
  }
  .contact { position: absolute; left: 290px; top: 62px; color: var(--white); }
  .contact__name { color: var(--navy-deep); font-size: 18px; line-height: 1.1; }
  .contact__title { color: var(--light-blue); font-size: 15px; margin-bottom: 12px; filter: brightness(.8); }
  .contact__address { font-size: 13px; line-height: 1.3; margin-bottom: 12px; }
  .contact__list { list-style: none; font-size: 13px; }
  .contact__item { display: flex; align-items: center; gap: 8px; line-height: 1.45; }
  .contact__icon { width: 12px; height: 12px; flex: none; }
  .contact__icon--blank { visibility: hidden; }
</style>
</head>
<body>
  <section class="card card--front" aria-label="Card front">
    <div class="brand">
      <div class="brand__name">ORVELL<span class="brand__dot"></span></div>
      <div class="brand__tag">A CLOUD CONSULTING COMPANY</div>
    </div>
    <div class="front__web">www.orvelltech.com</div>
  </section>

  <section class="card card--back" aria-label="Card back">
    <div class="brand">
      <div class="brand__name">ORVELL<span class="brand__dot"></span></div>
      <div class="brand__tag">A CLOUD CONSULTING COMPANY</div>
    </div>
    <div class="divider"></div>
    <div class="contact">
      <div class="contact__name">Marisakorvand</div>
      <div class="contact__title">Office Manager</div>
      <div class="contact__address">1187 N Larkspur Ave<br>Brookvale Ohio 43190</div>
      <ul class="contact__list">
        <li class="contact__item">
          <svg class="contact__icon" viewBox="0 0 12 12"><path fill="#1d4f80" d="M2 1h3l1 3-1.5 1a7 7 0 0 0 2.5 2.5L8 6l3 1v3a1 1 0 0 1-1 1A9 9 0 0 1 1 2a1 1 0 0 1 1-1z"/></svg>
          555.418.3027
        </li>
        <li class="contact__item">
          <svg class="contact__icon" viewBox="0 0 12 12"><rect x="1" y="4" width="10" height="6" rx="1" fill="#1d4f80"/><rect x="3" y="1" width="6" height="4" fill="#1d4f80"/></svg>
          555.418.3064
        </li>
        <li class="contact__item">
          <svg class="contact__icon" viewBox="0 0 12 12"><rect x="1" y="2.5" width="10" height="7" rx="1" fill="#1d4f80"/><path d="M1.5 3l4.5 3.5L10.5 3" stroke="#161718" fill="none"/></svg>
          mkorvand@orvelltech.com
        </li>
        <li class="contact__item">
          <svg class="contact__icon" viewBox="0 0 12 12"><circle cx="6" cy="6" r="5" fill="#1d4f80"/><path d="M1 6h10M6 1c-2 2.5-2 7.5 0 10M6 1c2 2.5 2 7.5 0 10" stroke="#161718" stroke-width=".8" fill="none"/></svg>
          www.orvelltech.com
        </li>
      </ul>
    </div>
  </section>
</body>
</html>
```